Packaging and labelling for Swiss made Organic CBD Oil

Visit our website www.clearleafmerida.example
We have not put any product on yet as require packaging and label design .
Website will give you a great feel for the company and how we have used
the logo . The Vextora cbd product shown is a company similar to ourselves with similar core values , we liked the clean packaging design they have .

Im happy if you want use the mandala symbol in our logo separate from
KELVORA, to separate and use the mandala symbol as a larger icon than
it appears in our logo
Clean , Pure , organic feel. Like the product to look pharmaceutical and life changing not gimmicky.
Colours to go with or be the same as our logo colours
But not too cold and clinical
Bottle size 84mm x 25mm
Label size 75mm x 30mm
Box 30mm x 30mm x 100mm
6 products
Full Spectrum :
500mg CBD (5%)
1000mg CBD ( 10% )
1500mg CBD (15%)
2000mg CBD ( 20% )
Broad spectrum THC Free
500mg CBD (5%)
Pets
500mg Broad Spectrum THC Free
Updates

Would like the design to be more modern than traditional

LABEL Information Front of Bottle - Logo KELVORA & Mandala - Mandala can be used separately as design symbol Organic Cannabis Oil 1500mg CBD (15%) Ful Spectrum 10ml Back of bottle Ingredients: Organic Cannabis Oil Extract Organic Sunflower Seed Oil THC - 0.2% Certified Swiss Organic Cultivation Shake well before use. Store in a cool , dry place and out of the each of children BOX information Front and rear Logo - KELVORA & Mandala - Mandala can be used separately as a design symbol Organic Cannabis Oil 1500mg CBD (15%) Full Spectrum Sides x 2 This product is a food supplement and is not intended to diagnose, treat, cure or prevent any disease If you are pregnant, lactating or taking any medication consult your health care practitioner Suitable for vegetarians and vegans Ingredients Organic Cannabis Oil extract Organis Sunflower Oil Store in a cool ,dry place, out of the reach of children Recommended Use 1-5 drops ( 1 drop = 7.5mg CBD ) Subject to body weight and personal requirement - visit www.clearleafmerida for more information 100% Natural 100% Organic GMO free 100% Vegan ( symbol with each ) Expiry date see bottle label Cultivated and manufactured in Switzerland

Target Market(s)

age 40 - 80

Font styles to use
Other font styles liked:
• In our website we have used Open Sans for the copy and Lato for headings .

Requirements
Must have
• look like an Industry leader
Kelvora will change the quality of peoples lives and in some cases may
even save lives so want look powerful and credible
Our Mission is - Through Delivering Pure , Premium , Organic products we will educate, inform and help people achieve healthier , happier lifestyles
Nice to have
• Colours to look good with our logo colours or be the same as our logo
colours
Logo Font - Avenir Black and Avenir Book

Font used in website - Content - Open Sans / Headings - Lato
If you have another font for the packaging information that will go well with
our logo, I'm happy for you to use your skills

```html
<!DOCTYPE html>
<html lang="en">
<head>
<meta charset="utf-8">
<title>Kelvora Organic Cannabis Oil – Packaging</title>
<link rel="stylesheet" href="https://fonts.googleapis.com/css2?family=Nunito+Sans:wght@800&family=Open+Sans:wght@300;400;600&display=swap">
<style>
  :root {
    --backdrop: #d6d6d6;
    --panel: #f4f4f4;
    --panel-edge: #c9cfcf;
    --ink: #4a4a4a;
    --ink-soft: #6a6a6a;
    --teal: #78c1c1;
    --teal-faint: #dcecec;
    --organic-green: #5aac4e;
    --swiss-red: #d8232a;
  }
  * { box-sizing: border-box; margin: 0; padding: 0; }
  html, body { width: 1200px; height: 1001px; overflow: hidden; background: var(--backdrop); }
  body { position: relative; font-family: "Open Sans", sans-serif; color: var(--ink); }

  .panel {
    position: absolute;
    background: var(--panel);
    border: 1px solid var(--panel-edge);
    overflow: hidden;
  }
  .decor-ring {
    position: absolute;
    border: 10px solid var(--teal-faint);
    border-radius: 50%;
  }

  /* box front */
  .box-front { left: 90px; top: 130px; width: 250px; height: 740px; }
  .box-front .decor-ring { width: 210px; height: 210px; left: 20px; top: 250px; }

  .brand { position: absolute; display: flex; align-items: center; gap: 8px; }
  .brand-name {
    font-family: "Nunito Sans", sans-serif; font-weight: 800;
    color: var(--ink-soft); letter-spacing: 2px;
  }
  .brand-dot { background: var(--teal); border-radius: 50%; }

  .box-front .brand { left: 24px; top: 70px; }
  .box-front .brand-name { font-size: 30px; }
  .box-front .brand-dot { width: 12px; height: 12px; }

  .badge { position: absolute; display: flex; gap: 4px; align-items: center; }
  .badge-organic { background: var(--organic-green); }
  .badge-swiss { background: var(--swiss-red); }

  .box-front .badge { left: 22px; top: 325px; }
  .box-front .badge-organic { width: 96px; height: 22px; }
  .box-front .badge-swiss { width: 22px; height: 22px; }

  .product-name { position: absolute; font-weight: 300; color: var(--ink); }
  .box-front .product-name { left: 20px; top: 352px; font-size: 30px; }

  .strength { position: absolute; font-weight: 300; color: var(--ink); }
  .box-front .strength { left: 22px; top: 600px; font-size: 16px; }
  .spectrum { position: absolute; font-weight: 300; color: var(--ink); }
  .box-front .spectrum { left: 20px; top: 624px; font-size: 26px; }
  .origin { position: absolute; left: 22px; top: 690px; font-size: 15px; font-weight: 300; }

  /* box side */
  .box-side { left: 340px; top: 130px; width: 250px; height: 740px; }
  .box-side .decor-ring { width: 200px; height: 200px; left: 25px; top: 120px; }
  .side-copy {
    position: absolute; left: 24px; top: 250px; width: 205px;
    font-size: 11.5px; line-height: 1.4; font-weight: 300; color: var(--ink);
  }
  .side-copy p { margin-bottom: 10px; }
  .side-copy strong { font-weight: 600; }
  .side-copy .lab-heading { color: var(--teal); font-size: 13px; font-weight: 400; margin-bottom: 2px; }
  .volume { position: absolute; left: 24px; top: 690px; font-size: 15px; font-weight: 300; }

  /* bottle label */
  .bottle-label { left: 640px; top: 395px; width: 480px; height: 192px; }
  .label-front { position: absolute; left: 140px; top: 0; width: 200px; height: 192px; }
  .bottle-label .decor-ring { width: 150px; height: 150px; left: 165px; top: 20px; }
  .fold-line { position: absolute; top: 0; width: 0; height: 100%; border-left: 1px dashed var(--panel-edge); }
  .bottle-label .brand { left: 14px; top: 14px; }
  .bottle-label .brand-name { font-size: 22px; }
  .bottle-label .brand-dot { width: 9px; height: 9px; }
  .bottle-label .badge { left: 14px; top: 64px; }
  .bottle-label .badge-organic { width: 72px; height: 16px; }
  .bottle-label .badge-swiss { width: 16px; height: 16px; }
  .bottle-label .product-name { left: 12px; top: 80px; font-size: 22px; }
  .bottle-label .strength { left: 14px; top: 130px; font-size: 12px; }
  .bottle-label .spectrum { left: 12px; top: 146px; font-size: 19px; }
</style>
</head>
<body>

<section class="panel box-front" aria-label="Box front panel">
  <div class="decor-ring" aria-hidden="true"></div>
  <div class="brand"><span class="brand-name">KELVORA</span><span class="brand-dot"></span></div>
  <div class="badge" aria-label="Organic and Swiss made certification">
    <span class="badge-organic"></span><span class="badge-swiss"></span>
  </div>
  <h1 class="product-name">Cannabis Oil</h1>
  <p class="strength">1500 mg CBD (15%)</p>
  <p class="spectrum">Full Spectrum</p>
  <p class="origin">Made in Switzerland</p>
</section>

<section class="panel box-side" aria-label="Box side panel">
  <div class="decor-ring" aria-hidden="true"></div>
  <div class="side-copy">
    <p>This product is a food supplement and is not intended to diagnose, treat, cure or prevent any disease.</p>
    <p>If you are pregnant, lactating or taking any medication consult your health care practitioner.</p>
    <p>Suitable for vegetarians and vegans.</p>
    <p><strong>Ingredients:</strong> Organic Cannabis Oil Extract, Organic Sunflower Oil</p>
    <p>Store in a cool, dry place, out of the reach of children.</p>
    <p class="lab-heading">Batch No and Lab Results</p>
    <p>Visit <strong>www.kelvoraorganic.example/labresults</strong> for independent third party lab test results for this product</p>
    <p>Batch No and expiry date see label on bottom of box</p>
  </div>
  <p class="volume">10 ml</p>
</section>

<section class="panel bottle-label" aria-label="Bottle label">
  <span class="fold-line" style="left:140px" aria-hidden="true"></span>
  <span class="fold-line" style="left:340px" aria-hidden="true"></span>
  <div class="decor-ring" aria-hidden="true"></div>
  <div class="label-front">
    <div class="brand"><span class="brand-name">KELVORA</span><span class="brand-dot"></span></div>
    <div class="badge" aria-label="Organic and Swiss made certification">
      <span class="badge-organic"></span><span class="badge-swiss"></span>
    </div>
    <h2 class="product-name">Cannabis Oil</h2>
    <p class="strength">1500 mg CBD (15%)</p>
    <p class="spectrum">Full Spectrum</p>
  </div>
</section>

</body>
</html>
```